Business Card Design

Hi I need a business card designed, we already have the business name logo artwork and would like some concept ideas for the Bus Card layout.
On the back of the card i want to include the products and services that we offer.
We are a Plastics Sheeting manufacture based in Perth Australia.

                                       

We need a BC design for a company called Tarvo Plastics based in Perth Australia.

We supply from DIY to Trade & Industrial  Engineering Markets.

We specialise in:

·         Cut to size panels  (all shapes and sizes)

·         Plastics fabrication & Welding

·         Custom Designs

·         Plastic Repairs

·         PVC Pipe Slotting & PVC Pipe Threading

·         Supplier of all types of engineering plastics and profiles.

Including:           Acrylic / Clarvene

                               Polycarbonate / Dorvil

                               Prismatic Light Diffuser

                               Vantrib

                               HDPE / UHMWPE

                               PVC / PVC Foam

                               Nylon

                               HIPS

```html
<!DOCTYPE html>
<html lang="en">
<head>
<meta charset="utf-8">
<title>Tarvo Plastics Business Card</title>
<link rel="stylesheet" href="https://fonts.googleapis.com/css2?family=Open+Sans:wght@400;600;700&display=swap">
<style>
  :root {
    --navy: #1c2a5c;
    --orange: #e8781e;
    --gold: #f2a81d;
    --white: #ffffff;
    --ink: #3a3a3a;
    --bg: #e9eaee;
    --divider: #8d95b3;
  }
  * { box-sizing: border-box; margin: 0; padding: 0; }
  html, body { width: 1200px; height: 987px; overflow: hidden; }
  body {
    background: var(--bg);
    font-family: "Open Sans", sans-serif;
    position: relative;
  }
  .card {
    position: absolute;
    left: 250px;
    width: 700px;
    height: 428px;
    border-radius: 22px;
    overflow: hidden;
    box-shadow: 0 6px 18px rgba(0,0,0,0.15);
  }
  /* Front */
  .card-front { top: 30px; background: var(--white); }
  .front-swoosh { position: absolute; inset: 0; width: 700px; height: 428px; }
  .brand-name {
    position: absolute;
    left: 200px; top: 28px;
    font-weight: 700;
    font-size: 62px;
    line-height: 1;
    color: var(--navy);
    letter-spacing: -1px;
  }
  .address {
    position: absolute;
    left: 44px; top: 128px;
    font-size: 17px;
    line-height: 1.4;
    color: var(--ink);
  }
  .contacts {
    position: absolute;
    left: 44px; top: 190px;
    list-style: none;
    font-size: 17px;
    line-height: 1.45;
    color: var(--ink);
  }
  .contacts li { display: flex; align-items: center; gap: 8px; }
  .contacts svg { width: 14px; height: 14px; fill: var(--ink); flex: none; }
  .contacts .mail-icon { fill: none; stroke: var(--ink); stroke-width: 1.6; }
  .person {
    position: absolute;
    left: 440px; top: 258px;
  }
  .person-name { font-weight: 600; font-size: 26px; color: var(--navy); }
  .person-title { font-size: 19px; color: var(--orange); margin-left: 70px; }
  .legal {
    position: absolute;
    left: 44px; top: 366px;
    font-size: 17px;
    line-height: 1.35;
    color: var(--white);
  }
  /* Back */
  .card-back { top: 518px; background: var(--navy); color: var(--white); }
  .back-brand {
    position: absolute;
    right: 40px; top: 22px;
    font-weight: 700;
    font-size: 52px;
    line-height: 1;
    color: var(--white);
    letter-spacing: -1px;
  }
  .tagline {
    position: absolute;
    left: 0; right: 0; top: 96px;
    text-align: center;
    font-weight: 700;
    font-size: 18px;
    line-height: 1.3;
  }
  .offer-col { position: absolute; top: 160px; }
  .offer-col.services { left: 36px; width: 330px; }
  .offer-col.materials { left: 410px; width: 270px; }
  .offer-heading { color: var(--gold); font-weight: 700; font-size: 21px; line-height: 1.2; margin-bottom: 4px; }
  .offer-list { list-style: none; font-size: 15.5px; line-height: 1.35; }
  .offer-list li { position: relative; padding-left: 14px; }
  .offer-list li::before {
    content: ""; position: absolute; left: 0; top: 8px;
    width: 7px; height: 7px; border-radius: 50%; background: var(--gold);
  }
  .dot { display: inline-block; width: 7px; height: 7px; border-radius: 50%; background: var(--gold); margin: 0 6px 2px 14px; }
  .divider {
    position: absolute; left: 385px; top: 170px;
    width: 1px; height: 220px; background: var(--divider);
  }
</style>
</head>
<body>

<section class="card card-front" aria-label="Business card front">
  <svg class="front-swoosh" viewBox="0 0 700 428" aria-hidden="true">
    <path d="M0,328 C200,342 420,350 560,428 L0,428 Z" fill="var(--navy)"/>
    <path d="M250,326 C420,330 540,368 610,428" fill="none" stroke="var(--orange)" stroke-width="5"/>
  </svg>
  <div class="brand-name">Tarvo Plastics</div>
  <p class="address">Unit 4/18 Brindle Circuit Halden Vale WA 6155<br>PO Box 2270 Halden Vale DC WA 6970</p>
  <ul class="contacts">
    <li><svg viewBox="0 0 16 16"><path d="M4 1l3 3-2 2c1 2 3 4 5 5l2-2 3 3-2 3C7 15 1 9 1 3z"/></svg>08 9400 1234</li>
    <li><svg viewBox="0 0 16 16"><rect x="4" y="1" width="8" height="14" rx="1.5"/></svg>0400 555 018</li>
    <li><svg viewBox="0 0 16 16"><rect x="1" y="6" width="14" height="8" rx="1"/><rect x="4" y="2" width="8" height="5"/></svg>08 9400 1235</li>
    <li><svg viewBox="0 0 16 16" class="mail-icon"><path d="M1.5 4h13v9h-13z M1.5 4l6.5 5 6.5-5"/></svg>sales@tarvoplastics.com.au</li>
  </ul>
  <div class="person">
    <div class="person-name">Your Name</div>
    <div class="person-title">Title</div>
  </div>
  <p class="legal">Corvain Holdings Pty Ltd<br>T/A Tarvo Plastics ABN: TBA</p>
</section>

<section class="card card-back" aria-label="Business card back">
  <div class="back-brand">Tarvo Plastics</div>
  <p class="tagline">The Products And Services That We Offer<br>Are Supplied From Diy To Trade &amp; Industrial Engineering Markets</p>
  <div class="offer-col services">
    <h2 class="offer-heading">We specialise in:</h2>
    <ul class="offer-list">
      <li>Cut to size panels (all shapes and sizes)</li>
      <li>Plastics fabrication &amp; Welding</li>
      <li>Custom Designs</li>
      <li>Plastic Repairs</li>
      <li>PVC Pipe Slotting &amp; PVC Pipe Threading</li>
      <li>Supplier of all types of engineering plastics and profiles</li>
    </ul>
  </div>
  <div class="divider"></div>
  <div class="offer-col materials">
    <h2 class="offer-heading">Including:</h2>
    <ul class="offer-list">
      <li>Acrylic / Clarvene</li>
      <li>Polycarbonate / Dorvil</li>
      <li>Prismatic Light Diffuser</li>
      <li>Vantrib<span class="dot"></span>HDPE / UHMWPE</li>
      <li>PVC / PVC Foam</li>
      <li>Nylon<span class="dot"></span>HIPS</li>
    </ul>
  </div>
</section>

</body>
</html>
```